Thornvale Group needs a business card design

We need a new business card design using the logo recently selected in a logo competition on Pixel Bazaar. Our business is a consultancy specializing in aviation and energy and the winning business card design will promote an image of precision and professionalism with creativity.

Please use the logo with the name on the front of the card and use a complementary font. Make the back white with either the light grey or dark grey logo.

Target Market(s)

Senior finance and legal leaders at aviation and energy companies

Industry/Entity Type

Management Consulting

Contact Information for Business Card

Peter Castrell
President
Thornvale Group

www.thornvalegroup.example

(555) 204-6391
pc@thornvalegroup.example

Requirements
Must have
• Professional font that goes well with the logo font

```html
<!DOCTYPE html>
<html lang="en">
<head>
<meta charset="utf-8">
<title>Thornvale Group – Business Card</title>
<link rel="stylesheet" href="https://fonts.googleapis.com/css2?family=Questrial&display=swap">
<style>
  :root {
    --page-bg: #ecebe8;
    --card-face: #d9dadb;
    --card-face-light: #e6e7e8;
    --card-edge: #c4c6c8;
    --brand-blue: #2b5583;
    --band-dark: #333435;
    --text-light: #ffffff;
    --text-blue: #2f5f93;
  }
  * { box-sizing: border-box; margin: 0; padding: 0; }
  html, body {
    width: 1200px;
    height: 800px;
    overflow: hidden;
    background: var(--page-bg);
    font-family: "Questrial", "Century Gothic", sans-serif;
  }
  .canvas {
    position: relative;
    width: 1200px;
    height: 800px;
  }
  .card {
    position: absolute;
    left: 150px;
    top: 143px;
    width: 900px;
    height: 514px;
    border-radius: 26px;
    overflow: hidden;
    background: linear-gradient(160deg, var(--card-face-light), var(--card-face));
    border: 2px solid var(--card-edge);
    box-shadow: 0 14px 40px rgba(0, 0, 0, 0.12);
  }
  .card-bands {
    position: absolute;
    inset: 0;
  }
  .brand-name {
    position: absolute;
    left: 0;
    right: 0;
    top: 130px;
    text-align: center;
    font-size: 44px;
    letter-spacing: 6px;
    color: var(--brand-blue);
    text-transform: uppercase;
  }
  .holder {
    position: absolute;
    left: 50px;
    top: 280px;
    width: 440px;
    color: var(--text-light);
  }
  .holder-name {
    font-size: 46px;
    line-height: 1.05;
    color: var(--text-light);
    white-space: nowrap;
  }
  .holder-name .surname { color: var(--text-blue); }
  .holder-title {
    font-size: 28px;
    color: var(--text-blue);
    margin-top: 2px;
  }
  .contact {
    position: absolute;
    left: 530px;
    top: 298px;
    width: 350px;
    list-style: none;
    color: var(--text-light);
    font-size: 21px;
  }
  .contact li {
    display: flex;
    align-items: center;
    gap: 12px;
    margin-bottom: 18px;
    white-space: nowrap;
  }
  .contact svg { flex: none; }
</style>
</head>
<body>
<main class="canvas">
  <article class="card">
    <svg class="card-bands" width="900" height="514" viewBox="0 0 900 514" aria-hidden="true">
      <rect class="accent-line-top" x="0" y="254" width="520" height="7" fill="var(--brand-blue)"/>
      <rect class="name-band" x="0" y="268" width="500" height="116" fill="var(--band-dark)"/>
      <rect class="contact-band" x="500" y="268" width="400" height="148" fill="var(--brand-blue)"/>
      <rect class="accent-line-bottom" x="0" y="392" width="500" height="6" fill="var(--band-dark)"/>
      <rect class="accent-line-base" x="0" y="426" width="900" height="5" fill="var(--brand-blue)"/>
    </svg>

    <div class="brand-name">Thornvale Group</div>

    <div class="holder">
      <p class="holder-name">Peter J. <span class="surname">Castrell</span></p>
      <p class="holder-title">President</p>
    </div>

    <ul class="contact">
      <li>
        <svg width="24" height="20" viewBox="0 0 24 20" aria-label="Phone">
          <path d="M2 6 Q12 -1 22 6 L19 9 L16 7 L16 5 Q12 3.5 8 5 L8 7 L5 9 Z" fill="#fff"/>
          <rect x="5" y="10" width="14" height="9" rx="2" fill="#fff"/>
        </svg>
        <span>(555) 204-6391</span>
      </li>
      <li>
        <svg width="24" height="18" viewBox="0 0 24 18" aria-label="Email">
          <rect x="1" y="1" width="22" height="16" fill="#fff"/>
          <path d="M1 1 L12 10 L23 1" fill="none" stroke="var(--brand-blue)" stroke-width="2"/>
        </svg>
        <span>pc@thornvalegroup.example</span>
      </li>
    </ul>
  </article>
</main>
</body>
</html>
```